Window company.

Hello,

We are a small family business located in Madrid, Spain that works nationwide to fix, change or mount the windows of your home / premises.

The group of possible clients to whom the flyer is focused ranges from 30 to 65 years, families in general who want comfort at home and extra savings every year in heating.

It must include not only graphics and a striking aesthetic in accordance with the concepts of wanting to reach / transmit the final product to the customer to sell the product.

Details to also include:

-Brief history of the company and its foundation in 2006. It will be subsequently translated into Spanish so put in words what you consider necessary so that the client stays with the concept that we are professionals.

--Specialized in exterior aluminum and PVC carpentry.

-We move to your home for a first visit and we provide the budget totally free without any commitment.

- Also payment facilities; up to 3 times, without interest.

-Contact details of the company. (WhatsApp, email, phone and location)
Open: Mon - Friday 11,00am - 9pm
Saturday: 12,00am - 7pm
Sunday: Closed

Also as a suggestion, to decide on your own, graphics of types of window openings, if you consider that anything that is striking for the client so it wonr be yet another advertising flyer.

We are open to all kinds of ideas, all of them involving marketing branding.

We are open to any type of idea and we want to stand out, the construction world is tough and we have an idea to grow, taking into account that it must not only be beautiful but commercial to attract potential customers with all kinds of purchasing power.

Thank you.

```html
<!DOCTYPE html>
<html lang="es">
<head>
<meta charset="utf-8">
<title>Ventalia – Carpintería de exterior</title>
<link href="https://fonts.googleapis.com/css2?family=Roboto+Condensed:wght@400;700&family=Roboto:wght@400;500;700&display=swap" rel="stylesheet">
<style>
  :root {
    --red: #c8302a;
    --ink: #3a3a3c;
    --grey-text: #8c8c8e;
    --panel: #efefef;
    --footer: #a3a3a5;
    --white: #ffffff;
  }
  * { margin: 0; padding: 0; box-sizing: border-box; }
  html, body { width: 848px; height: 1200px; overflow: hidden; background: var(--white); }
  .flyer {
    position: relative; width: 848px; height: 1200px; overflow: hidden;
    background: var(--white); font-family: "Roboto", Arial, sans-serif; color: var(--ink);
  }
  .abs { position: absolute; }

  /* Brand */
  .brand { left: 40px; top: 70px; display: flex; align-items: center; gap: 14px; }
  .brand-mark { width: 26px; height: 26px; background: var(--red); }
  .brand-name {
    font-family: "Roboto Condensed", Arial, sans-serif; font-weight: 700;
    font-size: 40px; letter-spacing: 3px; color: var(--grey-text);
  }
  .social { right: 28px; top: 38px; display: flex; gap: 22px; }
  .social span { width: 36px; height: 36px; border: 1.5px solid #b5b5b7; border-radius: 50%; }

  /* Hero */
  .hero-photo {
    left: 384px; top: 97px; width: 464px; height: 423px;
    background: linear-gradient(120deg, #f4f2ee 0%, #e6e2da 45%, #cfc6b8 75%, #b9ad9b 100%);
    clip-path: polygon(44px 0, 100% 0, 100% 100%, 0 100%, 0 71px);
  }
  .accent-line { left: 0; top: 0; }
  .headline {
    left: 36px; top: 204px;
    font-family: "Roboto Condensed", Arial, sans-serif; font-weight: 700;
    font-size: 45px; line-height: 51px; color: var(--ink); text-transform: uppercase;
  }
  .ribbon { left: 0; top: 373px; }
  .ribbon-text {
    left: 36px; top: 373px; height: 54px; line-height: 54px;
    font-family: "Roboto Condensed", Arial, sans-serif; font-size: 29px; color: var(--white);
  }
  .quality {
    left: 36px; top: 446px;
    font-family: "Roboto Condensed", Arial, sans-serif; font-weight: 700; font-size: 25px; color: var(--ink);
  }

  /* About */
  .about {
    left: 0; top: 520px; width: 848px; height: 195px;
    background: linear-gradient(180deg, #e9e9ea 0%, #f6f6f6 100%);
  }
  .about-title {
    left: 36px; top: 555px;
    font-family: "Roboto Condensed", Arial, sans-serif; font-weight: 700; font-size: 22px; color: var(--red);
  }
  .about-copy { left: 36px; top: 597px; width: 360px; font-size: 15.5px; line-height: 21px; }
  .divider { left: 423px; top: 548px; width: 1px; height: 164px; background: #c4c4c6; }
  .special-title {
    left: 444px; top: 553px; width: 380px;
    font-family: "Roboto Condensed", Arial, sans-serif; font-weight: 700; font-size: 16.5px; line-height: 20px;
    text-transform: uppercase;
  }
  .special-copy { left: 444px; top: 605px; width: 382px; font-size: 15.5px; line-height: 20px; text-align: justify; }
  .payment {
    left: 444px; top: 679px; width: 388px; height: 34px; line-height: 34px; text-align: center;
    background: var(--red); color: var(--white);
    font-family: "Roboto Condensed", Arial, sans-serif; font-weight: 700; font-size: 14.5px;
  }

  /* Services */
  .services-photo {
    left: 0; top: 776px; width: 848px; height: 242px;
    background: linear-gradient(180deg, #8a8c90 0%, #74777b 50%, #5e6164 100%);
  }
  .services-line { left: 0; top: 752px; width: 848px; height: 4px; background: var(--red); }
  .services-tab { left: 0; top: 737px; }
  .services-title {
    left: 36px; top: 737px; height: 40px; line-height: 40px;
    font-family: "Roboto Condensed", Arial, sans-serif; font-weight: 700; font-size: 24px; color: var(--white);
  }
  .services-bottom { left: 0; top: 1016px; width: 848px; height: 3px; background: var(--red); }
  .service {
    display: flex; align-items: center; gap: 20px;
    font-family: "Roboto Condensed", Arial, sans-serif; font-weight: 700; font-size: 21px; color: var(--white);
  }
  .service svg { width: 44px; height: 40px; flex: none; }

  /* Contact */
  .hours { left: 0; top: 1040px; width: 848px; text-align: center; font-size: 16px; color: #222; }
  .footer { left: 0; top: 1113px; width: 848px; height: 87px; background: var(--footer); }
  .call {
    left: 78px; top: 1093px; width: 680px; height: 42px; border-radius: 14px;
    background: var(--red); color: var(--white);
    display: flex; align-items: center; justify-content: center; gap: 8px;
    font-weight: 700; font-size: 19px;
  }
  .call .lead { font-family: "Roboto Condensed", Arial, sans-serif; font-size: 21px; margin-right: 6px; }
  .footer-lines {
    left: 0; top: 1142px; width: 848px; text-align: center; color: var(--white);
    font-size: 17px; line-height: 25px;
  }
</style>
</head>
<body>
<div class="flyer">

  <div class="abs brand"><span class="brand-mark"></span><span class="brand-name">VENTALIA</span></div>
  <div class="abs social" aria-hidden="true"><span></span><span></span><span></span><span></span></div>

  <div class="abs hero-photo" role="img" aria-label="Mujer relajada junto a una gran ventana blanca, con una taza en la mano"></div>
  <svg class="abs accent-line" width="848" height="200" viewBox="0 0 848 200" aria-hidden="true">
    <polyline points="0,168 370,168 428,97 848,97" fill="none" stroke="#c8302a" stroke-width="4"/>
  </svg>

  <h1 class="abs headline">Ahhore<br>todos los años en<br>confort</h1>
  <svg class="abs ribbon" width="424" height="54" viewBox="0 0 424 54" aria-hidden="true">
    <polygon points="0,0 396,0 424,54 0,54" fill="#c8302a"/>
  </svg>
  <div class="abs ribbon-text">Presupuestos sin compromiso</div>
  <div class="abs quality">CALIDAD GARANTIZADA !</div>

  <div class="abs about"></div>
  <h2 class="abs about-title">QUIENES SOMOS</h2>
  <p class="abs about-copy">Somos una empresa con más de 20 años en el sector carpintería de exterior entre otras.</p>
  <div class="abs divider"></div>
  <h3 class="abs special-title">Especializados en carpintería de aluminio exterior y carpintería de PVC.</h3>
  <p class="abs special-copy">Nos trasladamos a su vivienda para una primera visita y le proporcionamos un presupuesto totalmente gratuito.</p>
  <div class="abs payment">FACILIDADES DE PAGO; HASTA 3 VECES SIN INTERESES</div>

  <div class="abs services-photo" role="img" aria-label="Fachada de una casa con varias ventanas, en tonos grises"></div>
  <div class="abs services-line"></div>
  <svg class="abs services-tab" width="300" height="40" viewBox="0 0 300 40" aria-hidden="true">
    <polygon points="0,0 300,0 280,40 0,40" fill="#c8302a"/>
  </svg>
  <h2 class="abs services-title">NUESTROS SERVICIOS</h2>
  <div class="abs services-bottom"></div>

  <div class="abs service" style="left:44px;top:788px">
    <svg viewBox="0 0 44 40"><rect x="1" y="1" width="42" height="38" rx="5" fill="none" stroke="#fff" stroke-width="1.5"/><polygon points="10,20 22,10 34,20" fill="#c8302a"/><rect x="13" y="20" width="18" height="12" fill="#c8302a"/></svg>
    CARPINTERIA DE EXTERIOR</div>
  <div class="abs service" style="left:44px;top:843px">
    <svg viewBox="0 0 44 40"><rect x="1" y="1" width="42" height="38" rx="5" fill="none" stroke="#fff" stroke-width="1.5"/><path d="M10 12h24l3 8H7z" fill="#c8302a"/><rect x="11" y="22" width="22" height="10" fill="#c8302a"/></svg>
    TOLDOS</div>
  <div class="abs service" style="left:44px;top:898px">
    <svg viewBox="0 0 44 40"><rect x="1" y="1" width="42" height="38" rx="5" fill="none" stroke="#fff" stroke-width="1.5"/><rect x="12" y="8" width="20" height="25" fill="none" stroke="#c8302a" stroke-width="3"/><line x1="22" y1="8" x2="22" y2="33" stroke="#c8302a" stroke-width="2"/></svg>
    ALUMINIO</div>
  <div class="abs service" style="left:44px;top:953px">
    <svg viewBox="0 0 44 40"><rect x="1" y="1" width="42" height="38" rx="5" fill="none" stroke="#fff" stroke-width="1.5"/><rect x="11" y="9" width="22" height="22" fill="none" stroke="#c8302a" stroke-width="3"/><path d="M22 9v22M11 20h22" stroke="#c8302a" stroke-width="2.5"/></svg>
    DOBLE ACRISTALAMIENTO</div>

  <div class="abs service" style="left:425px;top:788px">
    <svg viewBox="0 0 44 40"><rect x="1" y="1" width="42" height="38" rx="5" fill="none" stroke="#fff" stroke-width="1.5"/><rect x="11" y="9" width="22" height="22" fill="none" stroke="#c8302a" stroke-width="3"/><path d="M22 9v22M11 20h22" stroke="#c8302a" stroke-width="2"/></svg>
    PVC</div>
  <div class="abs service" style="left:425px;top:843px">
    <svg viewBox="0 0 44 40"><rect x="1" y="1" width="42" height="38" rx="5" fill="none" stroke="#fff" stroke-width="1.5"/><rect x="11" y="9" width="22" height="22" fill="#c8302a"/><path d="M15 9v22M19 9v22M23 9v22M27 9v22M11 13h22M11 17h22M11 21h22M11 25h22" stroke="#e8928d" stroke-width="1"/></svg>
    MOSQUITERAS</div>
  <div class="abs service" style="left:425px;top:898px">
    <svg viewBox="0 0 44 40"><rect x="1" y="1" width="42" height="38" rx="5" fill="none" stroke="#fff" stroke-width="1.5"/><polygon points="11,10 30,10 33,31 14,31" fill="#c8302a"/></svg>
    CERRAMIENTOS</div>
  <div class="abs service" style="left:425px;top:953px">
    <svg viewBox="0 0 44 40"><rect x="1" y="1" width="42" height="38" rx="5" fill="none" stroke="#fff" stroke-width="1.5"/><path d="M22 12v16M14 20h16" stroke="#c8302a" stroke-width="3"/></svg>
    Y MUCHO MAS</div>

  <p class="abs hours">ABIERTO: LUNES - VIERNES 11:00 - 21:00 | SÁBADOS: 12:00 - 18:00 | DOMINGOS: CERRADO</p>

  <div class="abs footer"></div>
  <div class="abs call">
    <span class="lead">LLÁMENOS AL</span>
    <svg width="20" height="20" viewBox="0 0 24 24" aria-hidden="true"><circle cx="12" cy="12" r="10.5" fill="none" stroke="#fff" stroke-width="2"/><path d="M8.5 7c.6-.6 1.3-.4 1.6.2l.8 1.6c.2.5 0 1-.4 1.3l-.6.5c.5 1.3 1.6 2.4 2.9 2.9l.5-.6c.3-.4.8-.6 1.3-.4l1.6.8c.6.3.8 1 .2 1.6-1 1-2.5 1.3-4 .5-2-1-3.6-2.6-4.6-4.6-.8-1.5-.5-3 .7-3.8z" fill="#fff"/></svg>
    <span>+34 600 41 27 95 para mas información</span>
  </div>
  <p class="abs footer-lines">presupuestos@ventalia-ventanas.es | www.ventalia-ventanas.es<br>Polígono Las Arenas, Madrid</p>

</div>
</body>
</html>
```